Looking for a cool, modern Cannabis Jar Label

I want you to come up with a better, modern look for a label.

I need it sized to 4” x 3” - I plan to print directly to label printer.

I want you to use Photoshop and deliver me a layered PSD file that I can edit and modify the information as needed..

The label information will need to include places for:
(1) Strain Name - most important part of label - larger font size than rest - example Kestrel Mist, PLV #7, Juniper Hollow
(2) Pricing - for Gram, 1/8, 1/4, 1/2. and Ounce
(3) Strain Designation (Hybrid, Indica or Sativa) - maybe color coded, different color for Indica v. Sativa, just an idea
(4) THC and CBD percentages - for example 23% THC and 0.05% CBD
(5) Farm name - a place where we can add the name/logo of the business that produced the product. example - Ovenrow Farms

I have attached a simple mockup showing the information.

I have also attached a few samples of labels we like to give you an idea of the look and feel we are going for.

I am wanting a very clean, modern, classy, readable look.The font will use is Gotham Font.

HI Everyone! Thank you for all of your designs. I am requesting an extension because I need more time to give adequate feedback to the designers. Thank you for your participation and all of your efforts! I will be making a decision soon!

• Gotham Font

• Thank you for your designs. I am sorry i have been slow in providing feedback, things have been really busy around here!
• I wanted to give some group general feedback. After reviewing all of the designs, there is a common theme among all of the designs that I would like to see changed.
• I would like to see the per gram pricing more prominent on the label. This is what most people are looking for when they are purchasing the product. So I would like to see this stand out from the other pricing tiers. As I think about it, they don't all need to be grouped together in a line. You could have the Per Gram pricing front and center some where and then the other pricing tiers grouped together somewhere else on the label.
• This is the order of importance of items on the label. Items at the the top of the list should be bigger than those below it.
• 1. Strain name
• 2. Pricing - being per gram the most important of all prices
• 3. THC/CBD percentages
• 4. Strain Type (indica, sativa, hybrid)
• 5. Farm name/logo
• When laying out these labels, they will be going on rounded jars and they will be on display. Think of jars with fancy labels in a candy store. They need to be eye catchy, appealing, but easy read.
• Thank you for all of your hard work, everyone is doing a great job.
• Best,
• Neta

```html
<!DOCTYPE html>
<html lang="en">
<head>
<meta charset="utf-8">
<title>Kestrel Mist Jar Label</title>
<link rel="stylesheet" href="https://fonts.googleapis.com/css2?family=Montserrat:wght@400;500;700;800&family=Oswald:wght@400;600&display=swap">
<style>
  :root {
    --backdrop: #4d4d4d;
    --label: #ffffff;
    --green: #1a6b30;
    --ink: #0d0d0d;
    --muted: #555555;
    --rule: #222222;
    --divider: #9a9a9a;
    --brand: #333333;
    --mark: #f29a2e;
  }
  html, body {
    margin: 0;
    padding: 0;
    width: 1200px;
    height: 1200px;
    overflow: hidden;
    background: var(--backdrop);
  }
  .canvas {
    position: relative;
    width: 1200px;
    height: 1200px;
    background: var(--backdrop);
    font-family: "Montserrat", sans-serif;
    color: var(--ink);
  }
  .label {
    position: absolute;
    left: 100px;
    top: 220px;
    width: 1010px;
    height: 770px;
    background: var(--label);
  }
  .strain-name {
    position: absolute;
    left: 34px;
    top: 33px;
    width: 924px;
    height: 168px;
    border: 4px solid var(--green);
    border-radius: 26px;
    display: flex;
    align-items: center;
    justify-content: center;
    font-size: 90px;
    font-weight: 400;
    letter-spacing: 1px;
    white-space: nowrap;
  }
  .price {
    position: absolute;
    top: 252px;
    width: 240px;
    margin-left: -120px;
    text-align: center;
  }
  .price-amount {
    font-family: "Oswald", sans-serif;
    font-weight: 600;
    font-size: 74px;
    line-height: 1;
    letter-spacing: -1px;
    white-space: nowrap;
  }
  .price-amount sup {
    font-size: 34px;
    vertical-align: top;
    position: relative;
    top: 2px;
    margin-left: 1px;
  }
  .price-tier {
    margin-top: 22px;
    font-size: 34px;
    color: var(--muted);
    display: flex;
    align-items: center;
    justify-content: center;
    gap: 24px;
    white-space: nowrap;
  }
  .price-tier svg { width: 22px; height: 26px; }
  .strain-type {
    position: absolute;
    left: 38px;
    top: 436px;
    width: 334px;
    height: 282px;
  }
  .type-header {
    height: 70px;
    background: var(--green);
    border-radius: 14px 14px 0 0;
    color: #fff;
    font-size: 43px;
    font-weight: 400;
    text-align: center;
    line-height: 72px;
    letter-spacing: 1px;
  }
  .potency {
    height: 140px;
    display: flex;
  }
  .potency-value {
    flex: 1;
    text-align: center;
    font-family: "Oswald", sans-serif;
    font-weight: 400;
    font-size: 90px;
    line-height: 150px;
    letter-spacing: -2px;
    white-space: nowrap;
  }
  .potency-value small { font-size: 44px; letter-spacing: 0; }
  .potency-divider {
    position: absolute;
    left: 157px;
    top: 106px;
    width: 2px;
    height: 146px;
    background: var(--divider);
  }
  .potency-labels {
    height: 72px;
    background: var(--ink);
    border-radius: 0 0 16px 16px;
    display: flex;
    justify-content: space-between;
    padding: 0 22px 0 14px;
    color: #fff;
    font-weight: 800;
    font-size: 42px;
    line-height: 74px;
  }
  .producer {
    position: absolute;
    left: 396px;
    top: 432px;
    width: 564px;
    height: 286px;
    border-top: 2px solid var(--rule);
    border-bottom: 2px solid var(--rule);
  }
  .producer-tag {
    position: absolute;
    left: 118px;
    top: 0;
    width: 252px;
    height: 36px;
    background: var(--ink);
    border-radius: 0 0 12px 12px;
    color: #fff;
    font-size: 24px;
    font-weight: 500;
    text-align: center;
    line-height: 36px;
  }
  .farm {
    position: absolute;
    left: 50px;
    top: 80px;
    display: flex;
    align-items: center;
    gap: 22px;
  }
  .farm-mark {
    flex: none;
    width: 102px;
    height: 104px;
    background: var(--mark);
    border-radius: 14px;
  }
  .farm-name {
    font-size: 46px;
    font-weight: 700;
    color: var(--brand);
    line-height: 1;
    white-space: nowrap;
  }
  .harvest-date {
    position: absolute;
    left: 14px;
    bottom: 12px;
    font-size: 21px;
    color: var(--rule);
  }
</style>
</head>
<body>
<div class="canvas">
  <div class="label">
    <div class="strain-name">Kestrel Mist</div>

    <div class="price" style="left:140px">
      <div class="price-amount">€ 10<sup>.50</sup></div>
      <div class="price-tier">
        <svg viewBox="0 0 22 26" aria-hidden="true"><rect x="7" y="1" width="8" height="6" rx="2" fill="#555"/><rect x="2" y="7" width="18" height="18" rx="4" fill="#555"/></svg>
        <span>1/8</span>
      </div>
    </div>
    <div class="price" style="left:380px">
      <div class="price-amount">€ 15<sup>.00</sup></div>
      <div class="price-tier">1/4</div>
    </div>
    <div class="price" style="left:626px">
      <div class="price-amount">€ 20<sup>.00</sup></div>
      <div class="price-tier">1/2</div>
    </div>
    <div class="price" style="left:874px">
      <div class="price-amount">€ 27<sup>.00</sup></div>
      <div class="price-tier">Ounce</div>
    </div>

    <div class="strain-type">
      <div class="type-header">INDICA</div>
      <div class="potency">
        <div class="potency-value">23<small>%</small></div>
        <div class="potency-value">0.5<small>%</small></div>
      </div>
      <div class="potency-labels"><span>THC</span><span>CBD</span></div>
      <div class="potency-divider"></div>
    </div>

    <div class="producer">
      <div class="producer-tag">Cultivated By:</div>
      <div class="farm">
        <div class="farm-mark"></div>
        <div class="farm-name">Fennick Grow</div>
      </div>
      <div class="harvest-date">Harvested Date:</div>
    </div>
  </div>
</div>
</body>
</html>
```